Need a new company business card

I am looking for a new company business card. Front and back. With information on it as per below. Card should be professional. Yet clever. Simple. Modern design. Pim card, traditional size. OK with say, all black or all red backside.

Varnholt is an indie, bootstrapped magazine advancing the work of intersectional feminists busting their buts to create a just world through the power of enterprise and innovation.

Varnholt is the home and voice of entrepreneurial feminism and feminist innovators worldwide. Entrepreneurial feminists are people (of all genders) who see inequality as an innovation priority. They work to advance gender equity and/or who strive to integrate and practice feminist principles, pedagogy, values into their innovation and entrepreneurship work.
We are committed to this space being trans and queer inclusive, anti-racist, intersectional, brave, and safe. We welcome all allies. We value learning, edgy but civil discourse and integrative thinking skills.

Target Market(s)

feminists, business owners,

Industry/Entity Type

Publishing Company

Contact Information for Business Card

RD Tolliver
Founder/Publisher
4-237 Ashgrove Lane, Toronto, ON
M4T 2K8
publisher@varnholt.com
416-552-3019
www.varnholt.com

Font styles to use
Serif
Other font styles liked:
• Myriad Pro

Colors
ec1f27
000000
ffffff

Requirements
Must have
• logo
• use red, black white colours only.
Nice to have
• use the compass in pattern or creatively but not too busy please
Should not have
• Should not be too busy. Elegant.

```html
<!DOCTYPE html>
<html lang="en">
<head>
<meta charset="utf-8">
<title>Varnholt — Business Card</title>
<link rel="stylesheet" href="https://fonts.googleapis.com/css2?family=Source+Sans+3:wght@700&family=Roboto:wght@400&family=Roboto+Condensed:wght@700&family=EB+Garamond:wght@500&display=swap">
<style>
  :root{
    --brand-red:#ec1f27;
    --ink:#333333;
    --ink-soft:#555555;
    --paper:#f4f4f2;
    --white:#ffffff;
    --backdrop:#e4e1dc;
  }
  *{margin:0;padding:0;box-sizing:border-box}
  html,body{width:1200px;height:960px;overflow:hidden;background:var(--backdrop)}
  .canvas{position:relative;width:1200px;height:960px}
  .card{position:absolute;width:600px;height:343px;box-shadow:0 3px 8px rgba(0,0,0,.18)}
  .card--front{left:314px;top:113px;background:var(--paper)}
  .card--back{left:311px;top:472px;background:var(--brand-red)}

  .wordmark{position:absolute;font-family:"Source Sans 3",sans-serif;font-weight:700;letter-spacing:-1px;line-height:1;white-space:nowrap}
  .tagline{position:absolute;font-family:"EB Garamond",serif;font-weight:500;text-transform:uppercase;letter-spacing:1.2px;white-space:nowrap}
  .badge{position:absolute;border-radius:50%}

  .card--front .wordmark{left:146px;top:98px;font-size:74px;color:var(--ink)}
  .card--front .tagline{left:148px;top:172px;font-size:11px;color:var(--ink)}
  .card--front .badge{left:437px;top:75px;width:16px;height:16px;border:1.5px solid var(--ink)}

  .contact{position:absolute;top:270px;font-family:"Roboto",sans-serif;font-size:14.5px;line-height:20px;color:var(--ink-soft)}
  .contact__name{left:30px;top:267px;font-family:"Roboto Condensed",sans-serif;font-weight:700;font-size:20px;color:var(--ink);line-height:23px}
  .contact__role{display:block;font-size:17.5px;color:var(--brand-red)}
  .contact__address{left:189px;font-style:normal}
  .contact__reach{left:390px;list-style:none}
  .contact__reach li{display:flex;align-items:center;gap:8px}
  .contact__reach svg{width:14px;height:14px;fill:var(--ink)}

  .card--back .wordmark{left:344px;top:224px;font-size:54px;color:var(--white)}
  .card--back .tagline{left:344px;top:276px;font-size:8.5px;color:var(--white)}
  .card--back .badge{left:546px;top:208px;width:13px;height:13px;border:1.5px solid var(--white)}
  .web{position:absolute;left:342px;top:291px;font-family:"Roboto",sans-serif;font-size:15px;letter-spacing:5.4px;color:var(--white)}
</style>
</head>
<body>
<main class="canvas">
  <section class="card card--front" aria-label="Card front">
    <div class="wordmark">Varnholt</div>
    <span class="badge" aria-hidden="true"></span>
    <div class="tagline">Working Papers on Fair Enterprise</div>

    <div class="contact contact__name">RD TOLLIVER<span class="contact__role">Founder/Publisher</span></div>
    <address class="contact contact__address">4-237 Ashgrove Lane<br>Toronto, ON, M4T 2K8</address>
    <ul class="contact contact__reach">
      <li><svg viewBox="0 0 24 24" aria-hidden="true"><path d="M6.6 10.8a15.1 15.1 0 0 0 6.6 6.6l2.2-2.2c.3-.3.7-.4 1-.2 1.1.4 2.3.6 3.6.6.6 0 1 .4 1 1V20c0 .6-.4 1-1 1A17 17 0 0 1 3 4c0-.6.4-1 1-1h3.5c.6 0 1 .4 1 1 0 1.3.2 2.5.6 3.6.1.3 0 .7-.2 1z"/></svg>416-552-3019</li>
      <li><svg viewBox="0 0 24 24" aria-hidden="true"><path d="M2 6.5V19h20V6.5l-10 7z M2.5 5h19L12 11.6z"/></svg>publisher@varnholt.com</li>
    </ul>
  </section>

  <section class="card card--back" aria-label="Card back">
    <div class="wordmark">Varnholt</div>
    <span class="badge" aria-hidden="true"></span>
    <div class="tagline">Working Papers on Fair Enterprise</div>
    <div class="web">www.varnholt.com</div>
  </section>
</main>
</body>
</html>
```